Website Banner Redesign for Kelvra Cargo Depot

Business Name:
KELVRA CARGO DEPOT

About Us:
- We’re a proudly Australian company that designs and builds tough, reliable toolboxes for Utes, Trucks, and Campervans. Our products are made to handle harsh conditions and are trusted by tradies, off-roaders, and professional fleets across the country.

Project Goal:
- We want to refresh our homepage and category banners with bold, modern designs that better showcase our products and value proposition.

Why We’re Updating:
Our current banners show the products well, but we want to improve:
Visual impact and hierarchy
- Readability of text (especially on mobile)
- Clearer calls-to-action (CTAs)
- Brand messaging around “Built Tough”, “Aussie Made”, and “Custom Fit-Outs”

Target Audience:
- Tradespeople
- 4x4 & off-road enthusiasts
- Caravan & camping community
- Ute/Truck/Caravan dealerships
- Fleet and commercial buyers

Design Style We Want:
- Bold, confident, rugged
- Clean layout with clear focal points
- Strong product imagery (we’ll supply photos)
- Use of brand colors: Black, White, Red, Grey
- Professional, not too busy or cluttered

Banner Uses:
- Homepage hero banner
- Category landing pages

UTE TOOLBOXES - https://www.kelvracargo.com.au/aluminium-toolboxes/
Truck Boxes - https://www.kelvracargo.com.au/truck-toolboxes/
Canopies - https://www.kelvracargo.com.au/canopy/
Dog Boxes - https://www.kelvracargo.com.au/dog-boxes/
CAMPER BOXES - https://www.kelvracargo.com.au/camper-toolboxes/
Accessories - https://www.kelvracargo.com.au/accessories/

- Can be reused for desktop and mobile

Inspiration Style:
Think: 4x4 accessory brands, tough tradie gear, or clean eCommerce landing banners from premium auto suppliers.

Target Market(s)

All in Brief Above

Industry/Entity Type

Retail

Requirements
Must have
• A banner using our products only. A banner for each category, and 2 alternate banners for the home page.
Nice to have
• I have added some designs which i like..... Please take a look and take inspiration from them.

```html
<!DOCTYPE html>
<html lang="en">
<head>
<meta charset="utf-8">
<title>Kelvra Cargo Depot – Toolbox Banner</title>
<link rel="stylesheet" href="https://fonts.googleapis.com/css2?family=Rubik:wght@600;700&display=swap">
<style>
  :root {
    --page-bg: #f0f0f0;
    --plate-dark: #0d0d0f;
    --pink-light: #f63a7c;
    --pink-deep: #b3114f;
    --white: #ffffff;
    --tick-bg: #f5417f;
    --cta-top: #ffd21a;
    --cta-bottom: #ff9400;
    --cta-text: #2b2b2b;
  }
  * { box-sizing: border-box; margin: 0; padding: 0; }
  html, body {
    width: 1200px; height: 499px; overflow: hidden;
    background: var(--page-bg);
    font-family: "Rubik", sans-serif;
  }
  .banner {
    position: absolute; left: 55px; top: 114px;
    width: 1090px; height: 272px; overflow: hidden;
    background: var(--plate-dark);
  }
  .banner__backdrop { position: absolute; inset: 0; }
  .product-photo {
    position: absolute; left: 58px; top: 23px; width: 571px; height: 223px;
    background: linear-gradient(90deg, #d6d6d6 0%, #b8b8b8 26%, #222226 30%, #1a1a1e 58%, #c9c9c9 64%, #a6a6a6 100%);
    border-radius: 3px;
  }
  .flag-map {
    position: absolute; left: 652px; top: 86px; width: 60px; height: 48px;
    background: linear-gradient(135deg, #1f2f8f, #12206b);
    border-radius: 10px 18px 14px 8px;
  }
  .claims { list-style: none; }
  .claim {
    position: absolute; right: 97px; height: 50px;
    display: flex; align-items: center; white-space: nowrap;
    color: var(--white); font-weight: 700; font-size: 40px; line-height: 1;
  }
  .claim--tough { top: 28px; }
  .claim--aussie { top: 85px; }
  .claim--custom { top: 143px; }
  .tick { position: absolute; left: 1019px; width: 24px; height: 24px; }
  .tick--tough { top: 43px; }
  .tick--aussie { top: 98px; }
  .tick--custom { top: 157px; }
  .cta {
    position: absolute; left: 801px; top: 209px; width: 232px; height: 39px;
    border-radius: 20px;
    background: linear-gradient(180deg, var(--cta-top), var(--cta-bottom));
    display: flex; align-items: center; justify-content: center;
    color: var(--cta-text); font-weight: 700; font-size: 31px; letter-spacing: 0.5px;
    text-decoration: none;
  }
  .cta__screw { position: absolute; top: 12.5px; width: 14px; height: 14px; }
  .cta__screw--left { left: 8px; }
  .cta__screw--right { right: 8px; }
</style>
</head>
<body>
  <section class="banner" aria-label="Kelvra Cargo Depot toolboxes">
    <svg class="banner__backdrop" width="1090" height="272" viewBox="0 0 1090 272" aria-hidden="true">
      <defs>
        <linearGradient id="plate" x1="0" y1="0" x2="0" y2="1">
          <stop offset="0" stop-color="#1b1b1f"/><stop offset="1" stop-color="#050506"/>
        </linearGradient>
        <linearGradient id="pink" x1="0" y1="0" x2="0" y2="1">
          <stop offset="0" stop-color="#f63a7c"/><stop offset="1" stop-color="#b3114f"/>
        </linearGradient>
        <linearGradient id="band" x1="0" y1="0" x2="1" y2="0">
          <stop offset="0" stop-color="#7a0a38" stop-opacity="0"/><stop offset="0.35" stop-color="#7a0a38" stop-opacity="0.6"/><stop offset="1" stop-color="#6a0830" stop-opacity="0.85"/>
        </linearGradient>
      </defs>
      <rect width="1090" height="272" fill="url(#plate)"/>
      <polygon points="448,0 1090,0 1090,272 647,272" fill="url(#pink)"/>
      <polygon points="612,198 682,272 712,272 630,190" fill="#ff7aa8" opacity="0.55"/>
      <polygon points="448,0 470,0 500,38 490,44" fill="#ff6a9c" opacity="0.6"/>
      <polygon points="620,28 1043,28 1028,78 620,78" fill="url(#band)"/>
      <polygon points="620,85 1043,85 1028,135 620,135" fill="url(#band)"/>
      <polygon points="620,143 1043,143 1028,193 620,193" fill="url(#band)"/>
    </svg>

    <div class="product-photo" role="img" aria-label="Product photo: white, black and polished aluminium toolboxes with lids open on a checker-plate floor"></div>
    <div class="flag-map" role="img" aria-label="Australia map filled with the Australian flag"></div>

    <ul class="claims">
      <li class="claim claim--tough">Built Tough</li>
      <li class="claim claim--aussie">Aussie Made</li>
      <li class="claim claim--custom">Custom Fit-Outs</li>
    </ul>

    <svg class="tick tick--tough" viewBox="0 0 24 24" aria-hidden="true"><circle cx="12" cy="12" r="12" fill="var(--tick-bg)"/><path d="M6.5 12.5l3.5 3.5 7.5-7.5" fill="none" stroke="#fff" stroke-width="2.6" stroke-linecap="round" stroke-linejoin="round"/></svg>
    <svg class="tick tick--aussie" viewBox="0 0 24 24" aria-hidden="true"><circle cx="12" cy="12" r="12" fill="var(--tick-bg)"/><path d="M6.5 12.5l3.5 3.5 7.5-7.5" fill="none" stroke="#fff" stroke-width="2.6" stroke-linecap="round" stroke-linejoin="round"/></svg>
    <svg class="tick tick--custom" viewBox="0 0 24 24" aria-hidden="true"><circle cx="12" cy="12" r="12" fill="var(--tick-bg)"/><path d="M6.5 12.5l3.5 3.5 7.5-7.5" fill="none" stroke="#fff" stroke-width="2.6" stroke-linecap="round" stroke-linejoin="round"/></svg>

    <a class="cta" href="https://www.kelvracargo.com.au/aluminium-toolboxes/">
      <svg class="cta__screw cta__screw--left" viewBox="0 0 14 14" aria-hidden="true"><circle cx="7" cy="7" r="6.5" fill="#fff3c0" stroke="#6b4a00" stroke-width="1"/><path d="M4 7h6M7 4v6" stroke="#3a2a00" stroke-width="1.6"/></svg>
      BUY NOW
      <svg class="cta__screw cta__screw--right" viewBox="0 0 14 14" aria-hidden="true"><circle cx="7" cy="7" r="6.5" fill="#fff3c0" stroke="#6b4a00" stroke-width="1"/><path d="M4 7h6M7 4v6" stroke="#3a2a00" stroke-width="1.6"/></svg>
    </a>
  </section>
</body>
</html>
```